Dental specialist needs a sharp looking letterhead

I am looking for a letterhead to be used to send letters and communication between myself (a dental specialist) and other dentists.
My office is a state of the art dental specialty office.
I need to letterhead to also state:
Bertram L. Oswick DDS
2748 Tollard Avenue, Suite K
West Tollard, NY 14391
(716)392-5061
fax: (716)392-5087
oswickroot.com (**this email address may change)

i included my logo designs.
thank you

Target Market(s)

dentists

Industry/Entity Type

Communication

Requirements
Must have
• the included logo, whether the vertical or horizontal versions

```html
<!DOCTYPE html>
<html lang="en">
<head>
<meta charset="utf-8">
<title>Tollard Endodontics P.C. Letterhead</title>
<link rel="stylesheet" href="https://fonts.googleapis.com/css2?family=Bitter:wght@300;400;600&display=swap">
<style>
  :root {
    --ink: #1a1a1a;
    --ink-soft: #333333;
    --brand-blue: #45a2da;
    --brand-green: #8cc63f;
    --paper: #ffffff;
    --rule: #555555;
  }
  * { margin: 0; padding: 0; box-sizing: border-box; }
  html, body { width: 931px; height: 1200px; overflow: hidden; background: var(--paper); }
  .letterhead {
    position: relative;
    width: 931px;
    height: 1200px;
    background: var(--paper);
    font-family: "Bitter", Georgia, serif;
    color: var(--ink);
  }
  .brand {
    position: absolute;
    left: 34px;
    top: 52px;
    display: flex;
    align-items: center;
    gap: 12px;
  }
  .brand-dot {
    width: 22px;
    height: 22px;
    border-radius: 50%;
    background: var(--brand-blue);
  }
  .brand-name {
    font-size: 22px;
    font-weight: 600;
    color: var(--ink);
    letter-spacing: 0.2px;
  }
  .contact {
    position: absolute;
    top: 30px;
    right: 38px;
    display: flex;
    font-style: normal;
    font-size: 16px;
    font-weight: 300;
    color: var(--ink-soft);
    line-height: 26.5px;
    letter-spacing: -0.4px;
  }
  .contact-address {
    text-align: right;
    padding-right: 21px;
    border-right: 1px solid var(--rule);
  }
  .contact-lines {
    padding-left: 22px;
    list-style: none;
  }
  .contact-lines li { display: flex; align-items: center; gap: 9px; }
  .contact-icon { width: 14px; height: 14px; fill: var(--ink); flex: none; }
  .footer-band {
    position: absolute;
    left: 0;
    bottom: 0;
    width: 931px;
    height: 74px;
    background: var(--brand-blue);
    border-top: 5px solid var(--brand-green);
    box-shadow: 0 -3px 0 var(--paper);
  }
  .doctor-name {
    position: absolute;
    left: 60px;
    bottom: 24px;
    font-size: 23px;
    font-weight: 400;
    color: var(--paper);
    letter-spacing: 0.3px;
  }
</style>
</head>
<body>
<main class="letterhead">
  <header>
    <div class="brand">
      <span class="brand-dot"></span>
      <span class="brand-name">Tollard Endodontics P.C.</span>
    </div>
    <address class="contact">
      <div class="contact-address">
        <div>2748 Tollard Avenue</div>
        <div>Suite K</div>
        <div>West Tollard NY 14391</div>
      </div>
      <ul class="contact-lines">
        <li>
          <svg class="contact-icon" viewBox="0 0 16 16" aria-hidden="true"><path d="M3.5 1l3 3-1.6 1.8c.8 1.9 2.4 3.5 4.3 4.3L11 8.5l3 3-1.8 2.4C6.9 14 2 9.1 1.1 3.8z"/></svg>
          <span>716-392-5061</span>
        </li>
        <li>
          <svg class="contact-icon" viewBox="0 0 16 16" aria-hidden="true"><path d="M4 1h8v4H4zM1 6h14v6h-2v3H3v-3H1zm4 5v2h6v-2z"/></svg>
          <span>716-392-5087</span>
        </li>
        <li>
          <svg class="contact-icon" viewBox="0 0 16 16" aria-hidden="true"><path d="M1 3h14v1.5L8 9 1 4.5zM1 6.3l7 4.4 7-4.4V13H1z"/></svg>
          <span>oswickroot@mailbox.com</span>
        </li>
      </ul>
    </address>
  </header>

  <footer class="footer-band">
    <p class="doctor-name">Bertram L. Oswick, DDS</p>
  </footer>
</main>
</body>
</html>
```